I need a 6 x 11 postcard created that adheres to the design templates of the Federated parcel bureau. It will be mailed to scholars to encourage them to attend and present papers at the Marrowgate Indie International Film Festival's "Frame, Signal, and Score Conference." It must be provocative and engaging like a film festival poster. One option would be to high light the glitz of Hollywood and the appeal of the beach/shoreline in Long Beach but that's just one idea and I would love for the designer to just come with something original. It should be artistically compelling in that it would cause someone to keep the postcard even if they didn't care about the event. It must stand out in the mail and on a bulletin board.

You DO NOT have to use logo that I included and you do not have to stick with color schemes that are on logo.

My notes are in red on the document that includes the text.

the front can be portrait or landscape but back must be landscape. Also, designs submitted should include front and back.

You do not have to use the logo I included. If you do use the logo you can change the colors to fit your design Ideas.

The postcard will be sent to scholars who study and write about film, television, music, and digital media. We are inviting them to participate in a conference by selling them hollywood and the beaches of southern california.

Festival

• The design must be bold and inventive. Either ultramodern or just artistically appealing. The words 'Frame, Signal, and Score Conference" and "Call for Papers, Films, and Exhibitors Now Open!" must be clear on the front. It should be bright and inviting or classically beautiful (e.g. black and white).

It must match the Federated Parcel Bureau design requirements for 6 x 11 postcards
• This has got to be taken seriously by some very creative and intelligent people who love art, film, etc.

```html
<!DOCTYPE html>
<html lang="en">
<head>
<meta charset="utf-8">
<title>Frame, Signal, and Score Conference — Postcard Front and Back</title>
<link rel="stylesheet" href="https://fonts.googleapis.com/css2?family=Oswald:wght@200;300&display=swap">
<style>
  :root {
    --stage: #8f8687;
    --card-ink: #19191a;
    --card-mid: #3b3b3d;
    --card-soft: #6e6e70;
    --card-light: #dcdcdc;
    --type: #f4f4f4;
    --rule: rgba(244, 244, 244, 0.85);
    --paper: #efefef;
    --paper-line: #3a3a3a;
  }
  html, body {
    margin: 0;
    width: 1200px;
    height: 676px;
    overflow: hidden;
    background: var(--stage);
  }
  .postcard {
    position: absolute;
    top: 182px;
    width: 570px;
    height: 311px;
    overflow: hidden;
    box-shadow: 0 5px 14px rgba(0, 0, 0, 0.35);
    font-family: "Oswald", "Arial Narrow", sans-serif;
  }
  .postcard--front {
    left: 20px;
    background: var(--card-ink);
    color: var(--type);
  }
  .postcard--back {
    left: 610px;
    background: var(--paper);
  }
  .postcard__artwork {
    position: absolute;
    inset: 0;
    background:
      radial-gradient(ellipse 200px 95px at 95px 190px, rgba(235,235,235,0.9), rgba(235,235,235,0) 75%),
      radial-gradient(ellipse 120px 60px at 210px 150px, rgba(190,190,190,0.6), rgba(190,190,190,0) 75%),
      radial-gradient(ellipse 110px 45px at 445px 225px, rgba(225,225,225,0.7), rgba(225,225,225,0) 75%),
      radial-gradient(ellipse 160px 120px at 500px 90px, rgba(110,110,112,0.55), rgba(110,110,112,0) 75%),
      linear-gradient(150deg, var(--card-soft) 0%, var(--card-mid) 30%, var(--card-ink) 62%, #2c2c2e 100%);
  }
  .headline,
  .call {
    position: absolute;
    top: 26px;
    margin: 0;
    font-weight: 200;
    font-size: 24px;
    line-height: 1.05;
    letter-spacing: 0.3px;
    text-transform: uppercase;
  }
  .headline { right: 236px; text-align: right; }
  .call { left: 350px; }
  .divider {
    position: absolute;
    left: 342px;
    top: 22px;
    width: 1px;
    height: 168px;
    background: var(--rule);
  }
  .detail {
    position: absolute;
    margin: 0;
    font-weight: 300;
    font-size: 9px;
    line-height: 1.25;
    letter-spacing: 0.5px;
    text-transform: uppercase;
  }
  .detail--dates { top: 138px; right: 236px; text-align: right; }
  .detail--deadline { top: 166px; right: 236px; text-align: right; }
  .detail--venue { top: 138px; left: 350px; }
  .website {
    position: absolute;
    left: 18px;
    bottom: 12px;
    margin: 0;
    font-weight: 300;
    font-size: 7px;
    letter-spacing: 1.6px;
    text-transform: uppercase;
  }
  .back__divider {
    position: absolute;
    left: 285px;
    top: 30px;
    width: 1px;
    height: 250px;
    background: var(--paper-line);
  }
  .back__stamp {
    position: absolute;
    right: 24px;
    top: 24px;
    width: 52px;
    height: 60px;
    border: 1px solid var(--paper-line);
    box-sizing: border-box;
  }
  .back__address {
    position: absolute;
    left: 310px;
    right: 30px;
    top: 150px;
    margin: 0;
    padding: 0;
    list-style: none;
  }
  .back__address li {
    height: 26px;
    border-bottom: 1px solid var(--paper-line);
  }
</style>
</head>
<body>
  <article class="postcard postcard--front">
    <div class="postcard__artwork" role="img" aria-label="Black and white ink-splash photograph layered over a faceted geometric cube pattern"></div>
    <h1 class="headline">Frame, Signal,<br>and Score<br>Conference</h1>
    <div class="divider"></div>
    <h2 class="call">Call for<br>Papers, Films,<br>and Exhibitors<br>Now Open!</h2>
    <p class="detail detail--dates">September 2-6,<br>2015</p>
    <p class="detail detail--deadline">Paper Deadline<br>April 1, 2015</p>
    <p class="detail detail--venue">Marrowgate,<br>California</p>
    <p class="website">www.marrowgateindie.com</p>
  </article>

  <article class="postcard postcard--back" aria-label="Postcard back for mailing">
    <div class="back__divider"></div>
    <div class="back__stamp"></div>
    <ul class="back__address">
      <li></li>
      <li></li>
      <li></li>
      <li></li>
    </ul>
  </article>
</body>
</html>
```